Summit Bodyform Gym Website

We need a website design for our gym.

Summit is the UAE's first calisthenics and parkour gym. The theme under which the gym revolves is that one does not require any machinery to workout as our bodies could be themselves the machinery. The gym is designed to be the more of a social hub rather than an "in-and-out" gym, where people come train, have fun, hang out and socialize for a few hours rather than just train for 60 minutes then leave. The gym is designed to be a big open space with lots of natural sunlight, natural wood and plants all over the place to create a natural and refreshing setting. We also use recycled material throughout the gym and recycle our waste as being green is part of our philosophy. We currently also have some of the world's top and most recognized calisthenics athletes working with us.

We would like our website to reflect all that as well as provide a simple, interactive and fun way for visitors to be able to get class and gym information, check out gym media and contact us for bookings.

Target Market(s)

Ages 15-35

Industry/Entity Type

Fitness

Coding

Coded - Design and coding required

Number of Pages Required

4 page

Font styles to use
Decorative

Colors
0792cd

Requirements
Must have
• Class descriptions
• Gym description
• Class schedules
• Trainer profiles
• Gym philosophy
• Contact Details
Nice to have
• A link to contact us directly for a free first trial class

```html
<!DOCTYPE html>
<html lang="en">
<head>
<meta charset="utf-8">
<title>Summit Bodyform Gym</title>
<link href="https://fonts.googleapis.com/css2?family=Oswald:wght@400;500&family=Open+Sans:wght@400;600&display=swap" rel="stylesheet">
<style>
:root{
  --brand:#0792cd;
  --brand-dark:#0680b4;
  --ink:#222222;
  --dark:#232323;
  --darker:#1a1a1a;
  --text:#555555;
  --muted:#9a9a9a;
  --light:#f1f2f3;
  --white:#ffffff;
}
*{box-sizing:border-box;margin:0;padding:0}
html,body{width:1200px;height:2683px;overflow:hidden;background:var(--white)}
body{font-family:"Open Sans",Arial,sans-serif;color:var(--text);position:relative}
.display{font-family:"Oswald","Arial Narrow",sans-serif;font-weight:400}
section,header,footer,nav{position:absolute;left:0;width:1200px}
.abs{position:absolute}
.btn{position:absolute;display:flex;align-items:center;justify-content:center;font-family:"Oswald","Arial Narrow",sans-serif;color:var(--white);text-decoration:none;white-space:nowrap}
.btn-brand{background:var(--brand)}
.btn-dark{background:var(--ink)}

/* header */
.site-header{top:0;height:118px;background:var(--white)}
.brand{left:75px;top:34px;display:flex;align-items:center;gap:12px}
.brand-mark{width:22px;height:22px;border-radius:50%;background:var(--brand)}
.brand-name{font-family:"Oswald","Arial Narrow",sans-serif;font-weight:500;font-size:40px;color:var(--ink);line-height:1}
.header-cta{left:676px;top:34px;width:239px;height:54px;font-size:24px}
.header-phone{position:absolute;left:955px;top:42px;display:flex;align-items:center;gap:14px;font-family:"Oswald","Arial Narrow",sans-serif;font-size:27px;line-height:36px;color:var(--ink);white-space:nowrap}

/* nav */
.main-nav{top:118px;height:57px;background:var(--dark)}
.nav-list{list-style:none;display:flex;position:absolute;left:75px;top:0;height:57px}
.nav-list li{height:57px;display:flex;align-items:center;padding:0 26px;font-family:"Oswald","Arial Narrow",sans-serif;font-size:17px;color:var(--white);white-space:nowrap}
.nav-list li.active{background:var(--brand);padding:0 24px}
.social{right:75px;top:17px;display:flex;gap:14px}
.social span{width:22px;height:22px;background:var(--brand);border-radius:3px;display:block}

/* hero */
.hero{top:175px;height:436px;background:linear-gradient(180deg,#8a8c8e 0%,#6d6f71 45%,#4a4c4e 100%)}
.hero-title{top:82px;width:100%;text-align:center;font-size:54px;line-height:61px;color:var(--white);font-weight:500;text-shadow:0 2px 6px rgba(0,0,0,.45)}
.hero-cta{left:480px;top:227px;width:240px;height:56px;font-size:24px}
.dots{left:564px;top:395px;display:flex;gap:10px}
.dots span{width:12px;height:12px;border-radius:50%;background:var(--white)}
.dots span:first-child{background:var(--brand);border:2px solid var(--white)}

/* welcome */
.welcome{top:611px;height:195px;text-align:center}
.section-title{font-size:29px;color:var(--brand);width:100%;text-align:center;position:absolute}
.welcome .section-title{top:30px}
.welcome p{position:absolute;left:85px;width:1030px;top:85px;font-size:13.5px;line-height:27px;color:var(--text)}

/* classes */
.classes{top:806px;height:505px;background:var(--brand)}
.classes .section-title{top:38px;color:var(--white)}
.class-card{position:absolute;top:100px;width:331px}
.class-photo{width:331px;height:181px}
.class-card h3{margin-top:20px;font-size:25px;color:var(--white);font-weight:400}
.class-card p{margin-top:6px;font-size:13.5px;line-height:21.5px;color:#cfeaf6}
.class-card .btn{position:static;width:197px;height:41px;margin-top:28px;font-size:17px}

/* philosophy */
.philosophy{top:1311px;height:525px;background:var(--white)}
.philosophy .section-title{top:35px}
.philosophy p{position:absolute;top:92px;width:100%;text-align:center;font-size:13.5px}
.video-frame{position:absolute;left:256px;top:144px;width:688px;height:337px;border:4px solid #cfcfcf;background:linear-gradient(180deg,#6b4a30 0%,#3f5a2e 55%,#2b2b2b 100%)}
.play{position:absolute;left:50%;top:50%;transform:translate(-50%,-50%)}

/* trainers */
.trainers{top:1836px;height:347px;background:linear-gradient(90deg,var(--white) 0%,var(--light) 60%,#e4e8ea 100%)}
.trainers .heading{left:75px;top:30px;font-size:29px;color:var(--brand)}
.trainers .name{left:75px;top:84px;font-size:22px;color:var(--ink)}
.trainers p{left:75px;top:120px;width:470px;font-size:13.5px;line-height:26px;color:var(--text)}
.trainers .btn{top:258px;height:43px;font-size:17px}
.trainer-photo{left:540px;top:0;width:300px;height:347px;background:linear-gradient(180deg,#d8dde0 0%,#c8b9a8 40%,#2e2e2e 100%)}
.trainer-video{left:796px;top:90px;width:330px;height:196px;border:4px solid #d0d0d0;background:linear-gradient(180deg,#3e6e9e 0%,#9aa8b3 60%,#c9b9ab 100%)}
.arrows{left:1078px;top:20px;display:flex;gap:14px}

/* signup */
.signup{top:2183px;height:118px;background:var(--brand)}
.signup h2{left:75px;top:36px;font-size:28px;color:var(--white);white-space:nowrap}
.signup .field{left:368px;top:38px;width:533px;height:43px;background:var(--white);display:flex;align-items:center;padding-left:16px;font-size:13.5px;color:#444}
.signup .btn{left:926px;top:38px;width:200px;height:43px;font-size:17px}

/* footer */
.site-footer{top:2301px;height:320px;background:var(--dark)}
.foot-col{position:absolute;top:48px}
.foot-col h4{font-family:"Oswald","Arial Narrow",sans-serif;font-weight:400;font-size:28px;color:var(--white);margin-bottom:18px;white-space:nowrap}
.foot-col ul{list-style:none}
.foot-col li{font-size:13.5px;color:#c9c9c9;line-height:29.5px}
.foot-col .org{font-family:"Oswald","Arial Narrow",sans-serif;font-size:20px;color:var(--brand);margin-bottom:12px;white-space:nowrap}
.foot-col address{font-style:normal;font-size:13.5px;color:#c9c9c9;line-height:24px;width:240px}
.map{left:778px;top:48px;width:348px;height:245px;border:4px solid #d8d8d8;background:linear-gradient(135deg,#bcd3e3 0%,#e8e4d8 45%,#dcd7c8 100%)}
.copyright{top:2621px;height:62px;background:var(--darker);display:flex;align-items:center;justify-content:center;font-size:12px;color:#777}
</style>
</head>
<body>

<header class="site-header">
  <div class="brand abs"><span class="brand-mark"></span><span class="brand-name">Summit</span></div>
  <a class="btn btn-brand header-cta" href="#">Free First Trial Class</a>
  <div class="header-phone">
    <svg width="20" height="20" viewBox="0 0 24 24"><rect x="0" y="0" width="24" height="24" rx="4" fill="#222"/><path d="M8 5l2 4-1.5 1.5c1 2 2.5 3.5 4.5 4.5L14.5 13.5l4 2-1 3c-6 0-11-5-11-11z" fill="#fff"/></svg>
    <span>1800-555-0142</span>
  </div>
</header>

<nav class="main-nav">
  <ul class="nav-list">
    <li class="active">Home</li><li>Class</li><li>Gym</li><li>Class Schedules</li><li>Trainer Profiles</li><li>Gym Philosophy</li><li>Contact</li>
  </ul>
  <div class="social abs"><span></span><span></span><span></span><span></span><span></span></div>
</nav>

<section class="hero" role="img" aria-label="Photo of the open training floor with calisthenics rigs, rings and a climbing net">
  <h1 class="hero-title display abs">Summit is the UAE's First Calisthenics<br>&amp; Parkour Gym</h1>
  <a class="btn btn-brand hero-cta" href="#">Free First Trial Class</a>
  <div class="dots abs"><span></span><span></span><span></span><span></span></div>
</section>

<section class="welcome">
  <h2 class="section-title display">Welcome to Our Website</h2>
  <p>Aliquam molestie, mi et imperdiet euismod, dui purus auctor tellus, et interdum lacus lectus et ante. Sed accumsan sollicitudin sapien, sit amet adipiscing turpis gravida ac. In congue, neque ac lobortis volutpat, libero mauris varius mi, vitae suscipit ipsum ligula vitae risus. Duis aliquam nibh a dui iaculis viverra id a velit. Vivamus egestas risus in magna varius commodo. Sed semper viverra egestas. Etiam pretium porttitor lectus, vel ornare neque porta volutpat.</p>
</section>

<section class="classes">
  <h2 class="section-title display">About Class</h2>
  <article class="class-card" style="left:75px">
    <div class="class-photo" role="img" aria-label="Photo of members lifting dumbbells in a strength class" style="background:linear-gradient(135deg,#d9d9d9,#6a5a50 60%,#3a3a3a)"></div>
    <h3 class="display">Heading Title</h3>
    <p>Duis aliquam nibh a dui iaculis viverra id a velit. Vivamus egestas risus in magna varius commodo. Sed semper viverra egestas.</p>
    <a class="btn btn-dark" href="#">Free First Trial Class</a>
  </article>
  <article class="class-card" style="left:434px">
    <div class="class-photo" role="img" aria-label="Photo of a trainer coaching a member on an exercise ball" style="background:linear-gradient(135deg,#8a6a55,#c98a55 55%,#3a3030)"></div>
    <h3 class="display">Heading Title</h3>
    <p>Duis aliquam nibh a dui iaculis viverra id a velit. Vivamus egestas risus in magna varius commodo. Sed semper viverra egestas.</p>
    <a class="btn btn-dark" href="#">Free First Trial Class</a>
  </article>
  <article class="class-card" style="left:796px">
    <div class="class-photo" role="img" aria-label="Photo of a group fitness class with light weights" style="background:linear-gradient(135deg,#e6e6e6,#d87a92 55%,#5a5a5a)"></div>
    <h3 class="display">Heading Title</h3>
    <p>Duis aliquam nibh a dui iaculis viverra id a velit. Vivamus egestas risus in magna varius commodo. Sed semper viverra egestas.</p>
    <a class="btn btn-dark" href="#">Free First Trial Class</a>
  </article>
</section>

<section class="philosophy">
  <h2 class="section-title display">Gym Philosophy</h2>
  <p>Aliquam molestie, mi et imperdiet euismod, dui purus auctor tellus, et interdum lacus lectus et ante.</p>
  <div class="video-frame" role="img" aria-label="Video still of the gym's living plant wall above a dumbbell rack">
    <svg class="play" width="64" height="64" viewBox="0 0 64 64"><circle cx="32" cy="32" r="28" fill="none" stroke="#fff" stroke-width="5"/><path d="M26 19l19 13-19 13z" fill="#fff"/></svg>
  </div>
</section>

<section class="trainers">
  <h2 class="heading display abs">Trainer Profiles</h2>
  <h3 class="name display abs">Trainer Name Heading</h3>
  <p class="abs">Aliquam molestie, mi et imperdiet euismod, dui purus auctor tellus, et interdum lacus lectus et ante. Sed accumsan sollicitudin sapien, sit amet adipiscing turpis gravida ac.Aliquam molestie, mi et imperdiet euismod, dui purus auctor tellus, et interdum lacus lectus et ante.</p>
  <a class="btn btn-dark" href="#" style="left:75px;width:143px">Read More Info</a>
  <a class="btn btn-dark" href="#" style="left:227px;width:136px">Watch Video</a>
  <div class="trainer-photo abs" role="img" aria-label="Photo of a smiling trainer with a towel over his shoulders"></div>
  <div class="trainer-video abs" role="img" aria-label="Video still of a trainer with a class using exercise balls">
    <svg class="play" width="54" height="54" viewBox="0 0 64 64"><circle cx="32" cy="32" r="28" fill="none" stroke="#fff" stroke-width="5"/><path d="M26 19l19 13-19 13z" fill="#fff"/></svg>
  </div>
  <div class="arrows abs">
    <svg width="16" height="24" viewBox="0 0 16 24"><path d="M13 3L4 12l9 9" fill="none" stroke="#777" stroke-width="3.5"/></svg>
    <svg width="16" height="24" viewBox="0 0 16 24"><path d="M3 3l9 9-9 9" fill="none" stroke="#777" stroke-width="3.5"/></svg>
  </div>
</section>

<section class="signup">
  <h2 class="display abs">Get Sign In For Free Class</h2>
  <div class="field abs">Enter Your Email</div>
  <a class="btn btn-dark" href="#">Get Started</a>
</section>

<footer class="site-footer">
  <div class="foot-col" style="left:75px">
    <h4>Navigation</h4>
    <ul><li>Home</li><li>Class</li><li>Gym</li><li>Class Schedules</li><li>Trainer Profiles</li><li>Gym Philosophy</li><li>Contact</li></ul>
  </div>
  <div class="foot-col" style="left:304px">
    <h4>Connect Us</h4>
    <ul><li>Social Feed</li><li>Quick Posts</li><li>Work Network</li><li>Circles</li><li>Video Channel</li></ul>
  </div>
  <div class="foot-col" style="left:524px">
    <h4>Contact Information</h4>
    <div class="org">Summit Bodyform Gym</div>
    <address>4127 Cedarline Avenue,<br>Dubai, DX 20417<br>Ph: 1800-555-0142<br>Email: info@summitgym.example</address>
  </div>
  <div class="map abs" role="img" aria-label="Map of the gym's location in Dubai"></div>
</footer>

<div class="copyright abs" style="left:0;width:1200px">Copyright © 2015. Company Name All Right Reserved</div>

</body>
</html>
```